Profesional personal website needs design and business card

I need a business card with my professional name as a logo "Dorian Vitality" for my business. I am a Wellness Coach, consultant and trainer. So it should be professional, wellness oriented and modern.

Target Market(s)

Private clients, governments, corporations. Luxury and high market.

Industry/Entity Type

Health And Wellness

Contact Information for Business Card

Dorian Vitality should be the logo

Colors

Designer to choose colors to be used in the design.

Requirements
Must have
• Dorian Vitality
• Name: Tomás Lirandel
• Wellness Coach, Consultant & Trainer.
• Website: www.dorianvitality-example.com
• Phone:
• Spain (+34) 612 480 317
• (USA) +1 (555) 610 4829
Nice to have
• The most important is the design of "Dorian Vitality", as this is going to be my personal brand logo. It should be professional, wellness, high end and actual.
Should not have
• no golds, no baroque style..

```html
<!DOCTYPE html>
<html lang="en">
<head>
<meta charset="utf-8">
<title>Dorian Vitality — Business Card</title>
<link rel="stylesheet" href="https://fonts.googleapis.com/css2?family=Roboto:wght@400&family=Roboto+Condensed:wght@700&family=Poppins:wght@500&display=swap">
<style>
  :root {
    --ocean: #1a7bad;
    --sky: #27a4dc;
    --ink: #111111;
    --paper: #ffffff;
  }
  html, body {
    margin: 0;
    padding: 0;
    width: 1000px;
    height: 1200px;
    overflow: hidden;
    background: var(--paper);
  }
  .canvas {
    position: relative;
    width: 1000px;
    height: 1200px;
  }
  .card {
    position: absolute;
    left: 124px;
    width: 751px;
    height: 501px;
    display: block;
  }
  .card--front { top: 72px; }
  .card--back  { top: 641px; }
  .band { fill: var(--ocean); }
  .paper { fill: var(--paper); }
  .stripe--sky   { stroke: var(--sky); fill: none; }
  .stripe--paper { stroke: var(--paper); fill: none; }
  .brand-name {
    font-family: "Roboto Condensed", "Arial Narrow", sans-serif;
    font-weight: 700;
    font-size: 74px;
    fill: var(--ocean);
  }
  .brand-dot { fill: var(--sky); }
  .person-name {
    font-family: "Roboto Condensed", "Arial Narrow", sans-serif;
    font-weight: 700;
    font-size: 100px;
    fill: var(--sky);
  }
  .person-role {
    font-family: "Poppins", sans-serif;
    font-weight: 500;
    font-size: 28px;
    fill: var(--ink);
  }
  .contact-text {
    font-family: "Roboto", sans-serif;
    font-weight: 400;
    font-size: 37px;
    fill: var(--ink);
  }
  .icon-disc { fill: var(--sky); }
  .icon-mark { fill: var(--ink); }
  .icon-line { stroke: var(--sky); fill: none; stroke-width: 3; }
</style>
</head>
<body>
<main class="canvas">

  <!-- Front of the card -->
  <svg class="card card--front" viewBox="0 0 1314 876" aria-label="Business card front">
    <rect class="paper" width="1314" height="876"/>
    <polygon class="band" points="628,0 1314,0 1314,228 667,876 0,876 0,627"/>
    <polygon class="paper" points="657,26 1053,422 657,818 261,422"/>

    <line class="stripe--sky" x1="-10" y1="593" x2="208" y2="376" stroke-width="20"/>
    <line class="stripe--sky" x1="228" y1="356" x2="612" y2="-28" stroke-width="20" stroke-dasharray="18 22"/>

    <line class="stripe--sky" x1="708" y1="886" x2="1113" y2="481" stroke-width="20"/>
    <line class="stripe--sky" x1="1132" y1="462" x2="1330" y2="264" stroke-width="20" stroke-dasharray="18 22"/>

    <g class="brand">
      <circle class="brand-dot" cx="657" cy="330" r="42"/>
      <text class="brand-name" x="657" y="462" text-anchor="middle">Dorian Vitality</text>
    </g>
  </svg>

  <!-- Back of the card -->
  <svg class="card card--back" viewBox="0 0 1314 876" aria-label="Business card back">
    <rect class="paper" width="1314" height="876"/>
    <polygon class="band" points="0,0 634,0 0,634"/>
    <polygon class="band" points="1314,236 1314,876 674,876"/>

    <line class="stripe--paper" x1="-10" y1="595" x2="213" y2="372" stroke-width="16"/>
    <line class="stripe--paper" x1="232" y1="353" x2="620" y2="-35" stroke-width="18" stroke-dasharray="18 22"/>

    <line class="stripe--paper" x1="706" y1="886" x2="1118" y2="474" stroke-width="16"/>
    <line class="stripe--paper" x1="1136" y1="456" x2="1330" y2="262" stroke-width="18" stroke-dasharray="18 22"/>

    <g class="identity">
      <text class="person-name" x="1193" y="194" text-anchor="end">Tomás Lirandel</text>
      <text class="person-role" x="1193" y="241" text-anchor="end">Wellness Coach, Consultant &amp; Trainer</text>
    </g>

    <g class="contact contact--phone">
      <circle class="icon-disc" cx="148" cy="587" r="38"/>
      <path class="icon-mark" d="M130 565 c4-3 8-3 10 1 l6 10 c2 4 1 7-2 9 l-4 3 c3 8 9 14 17 18 l3-4 c2-3 6-4 9-2 l10 6 c4 2 4 6 1 10 l-5 6 c-3 3-8 4-13 2 c-18-7-31-20-38-38 c-2-5-1-10 2-13 z"/>
      <text class="contact-text" x="232" y="577">Spain  : (+34) 612 480 317</text>
      <text class="contact-text" x="232" y="621">USA    : +1 (555) 610 4829</text>
    </g>

    <g class="contact contact--web">
      <circle class="icon-disc" cx="150" cy="714" r="38"/>
      <circle class="icon-mark" cx="150" cy="714" r="26"/>
      <ellipse class="icon-line" cx="150" cy="714" rx="11" ry="26"/>
      <line class="icon-line" x1="124" y1="714" x2="176" y2="714"/>
      <line class="icon-line" x1="150" y1="688" x2="150" y2="740"/>
      <text class="contact-text" x="232" y="729">www.dorianvitality-example.com</text>
    </g>
  </svg>

</main>
</body>
</html>
```